Logo, Web and Mobile Designs for enterprise social media platform

All the details are in the attached document, please start reading the scope document first which explains what is this project about and the details about the needed deliverables, after that please read the UI_Requirements document which will detail what is expected regarding the coded web version since this is a coded contest, it is very important that you meet the UI requirements or suggest something else but we will need to agree first before working on the coded version

Good Luck

Target Market(s)

Enterprise Social Media

Industry/Entity Type

Media

Coding

Coded - Design and coding required

Number of Pages Required

5+ page

Font styles to use
Sans Serif

Requirements
Must have
• All the must haves are listed in the scope document so please check before you start

```html
<!DOCTYPE html>
<html lang="en">
<head>
<meta charset="utf-8">
<title>Teamora</title>
<link rel="stylesheet" href="https://fonts.googleapis.com/css2?family=PT+Serif&family=Raleway:wght@400;500;700&family=Open+Sans:wght@400&display=swap">
<style>
  :root {
    --blue-top: #2a93d3;
    --blue-bottom: #1874bb;
    --divider: rgba(255,255,255,0.22);
    --white: #ffffff;
    --ink: #333333;
    --body-text: #7a7a7a;
    --orange-top: #ffa41a;
    --orange-bottom: #f58a06;
    --btn-blue-top: #2e95d6;
    --btn-blue-bottom: #1a73b8;
    --footer-top: #1c6091;
    --footer-bottom: #0d2f50;
  }
  * { margin: 0; padding: 0; box-sizing: border-box; }
  html, body { width: 1200px; height: 1086px; overflow: hidden; background: var(--white); }
  .page { position: relative; width: 1200px; height: 1086px; overflow: hidden; }

  .site-header {
    position: absolute; left: 0; top: 0; width: 1200px; height: 110px;
    background: linear-gradient(to bottom, var(--blue-top), var(--blue-bottom));
  }
  .brand {
    position: absolute; left: 140px; top: 30px;
    font-family: "PT Serif", serif; font-size: 40px; color: var(--white); line-height: 1;
  }
  .main-nav { position: absolute; left: 435px; top: 0; height: 110px; display: flex; }
  .main-nav a {
    display: flex; align-items: center; height: 110px; padding: 0 14px;
    font-family: "Raleway", sans-serif; font-size: 16px; font-weight: 500;
    color: var(--white); text-decoration: none;
  }
  .main-nav a + a { border-left: 1px solid var(--divider); }

  .hero { position: absolute; left: 0; top: 110px; width: 1200px; height: 525px; }
  .hero-photo {
    position: absolute; inset: 0;
    background:
      radial-gradient(ellipse at 20% 70%, rgba(224,170,120,0.85), transparent 55%),
      radial-gradient(ellipse at 55% 30%, rgba(200,140,100,0.7), transparent 50%),
      radial-gradient(ellipse at 85% 40%, rgba(150,70,60,0.75), transparent 55%),
      linear-gradient(135deg, #3d5a7a 0%, #5a4038 45%, #3a2a2a 70%, #6a2a28 100%);
  }
  .hero-shade { position: absolute; inset: 0; background: rgba(0,0,0,0.18); }
  .hero-kicker, .hero-title {
    position: absolute; left: 0; width: 1238px; text-align: center;
    font-family: "Raleway", sans-serif; font-weight: 700; color: var(--white);
    text-transform: uppercase; line-height: 1;
  }
  .hero-kicker { top: 145px; font-size: 30px; }
  .hero-title { top: 188px; font-size: 45px; }
  .hero-actions { position: absolute; top: 257px; left: 414px; display: flex; gap: 8px; }
  .btn {
    display: flex; align-items: center; justify-content: center; height: 43px;
    font-family: "Raleway", sans-serif; font-weight: 700; font-size: 15px;
    color: var(--white); text-decoration: none; text-transform: uppercase;
  }
  .btn-subscribe { width: 183px; background: linear-gradient(var(--orange-top), var(--orange-bottom)); }
  .btn-post { width: 183px; background: linear-gradient(var(--btn-blue-top), var(--btn-blue-bottom)); }
  .slider-dots { position: absolute; top: 481px; left: 553px; display: flex; gap: 4px; }
  .slider-dots span { width: 19px; height: 19px; border-radius: 50%; background: var(--white); }

  .about { position: absolute; left: 0; top: 635px; width: 1200px; height: 323px; text-align: center; }
  .about-title {
    margin-top: 48px; font-family: "PT Serif", serif; font-weight: 400;
    font-size: 40px; color: var(--ink); line-height: 1; padding-left: 12px;
  }
  .about-text {
    width: 860px; margin: 0 auto; padding-left: 12px;
    font-family: "Open Sans", sans-serif; font-size: 13.4px; line-height: 22px; color: var(--body-text);
  }
  .about-text:first-of-type { margin-top: 25px; }
  .about-text + .about-text { margin-top: 12px; }

  .site-footer {
    position: absolute; left: 0; top: 958px; width: 1200px; height: 128px;
    background: linear-gradient(to bottom, var(--footer-top), var(--footer-bottom));
  }
  .footer-nav { position: absolute; left: 155px; top: 34px; display: flex; gap: 25px; }
  .footer-nav a {
    font-family: "Raleway", sans-serif; font-weight: 500; font-size: 15px;
    color: var(--white); text-decoration: none;
  }
  .copyright {
    position: absolute; left: 155px; top: 64px;
    font-family: "Open Sans", sans-serif; font-size: 12.5px; color: var(--white);
  }
  .social { position: absolute; left: 958px; top: 38px; display: flex; gap: 12px; }
  .social a { display: block; width: 18px; height: 18px; border-radius: 50%; background: var(--white); }
</style>
</head>
<body>
<div class="page">
  <header class="site-header">
    <div class="brand">Teamora</div>
    <nav class="main-nav">
      <a href="#">About</a>
      <a href="#">Post New Event</a>
      <a href="#">Share Now</a>
      <a href="#">Participate</a>
      <a href="#">Members</a>
    </nav>
  </header>

  <section class="hero">
    <div class="hero-photo" role="img" aria-label="Photo of a group of smiling friends celebrating at a party with falling confetti"></div>
    <div class="hero-shade"></div>
    <p class="hero-kicker">Donec dictum lectus non odio</p>
    <h1 class="hero-title">Mauris vel lacus vitae felis</h1>
    <div class="hero-actions">
      <a class="btn btn-subscribe" href="#">Subscribe Event</a>
      <a class="btn btn-post" href="#">Post Your Event</a>
    </div>
    <div class="slider-dots"><span></span><span></span><span></span><span></span></div>
  </section>

  <section class="about">
    <h2 class="about-title">Little About Teamora</h2>
    <p class="about-text">Mauris vel lacus vitae felis vestibulum volutpat E&nbsp; eu imperdiet ac nisl Cum sociis natoque penatibus et magnis dis parturient montes nascetur ridiculus mus In iaculis facilisis massa Etiam eu urna Sed porta Suspendisse quam leo molestie sed luctus quis feugiat in pede Fusce tellus Sed metus augue convallis et vehicula ut pulvinar eu ante Integer orci tellus tristique vitae consequat nec</p>
    <p class="about-text">Vivamus porttitor purus nisi eleifend libero a tempus libero lectus feugiat felis Morbi diam mauris viverra in gravida eu mattis in ante Morbi eget arcu Morbi porta libero id ullamcorper nonummy nibh ligula pulvinar metus eget consectetuer augue nisi quis lacus Ut</p>
  </section>

  <footer class="site-footer">
    <nav class="footer-nav">
      <a href="#">About</a>
      <a href="#">Post New Event</a>
      <a href="#">Share Now</a>
      <a href="#">Participate</a>
      <a href="#">Members</a>
    </nav>
    <p class="copyright">© 2015 Company Name&nbsp; All right reserved&nbsp; Term of Use</p>
    <div class="social">
      <a href="#" aria-label="Social link 1"></a>
      <a href="#" aria-label="Social link 2"></a>
      <a href="#" aria-label="Social link 3"></a>
      <a href="#" aria-label="Social link 4"></a>
    </div>
  </footer>
</div>
</body>
</html>
```